Window Treatment business needs website redesigned.

We need a revamp and refresh of our current site www.velmarix.ca
Looking to attract very high end customer. It should be a very simple design with very little text. This site will be visited by prospective homeowners, designers, builders and architects. They should feel that they are dealing with a high-end product selection, where experience, customer service and unique product offering is the focus. The content will be to highlight our services and highlight the manufacturers we sell, using a few rich photos to highlight the products. We should NOT look like we are a very large company. It should NOT have discounts/savings buttons and many menus to choose from. We offer over 15 years experience to narrow the many market options, to provide the right technical solution.
We specialize in products that are not readily available on the market and specifically motorized systems for indoors and outdoors.
Our main suppliers are Kravenholt.com, Dimbrell.com
We carry our own locally manufactured product line of roller shades.
Main product pictures should be of roller shades, outdoor bug screens, awnings and outdoor pergolas.

Reason: I understand that Christmas is coming up real short and many people are extremely busy. If you have a CREATIVE gifting you still want to submit, I look forward to your idea!

Reason: Due to holiday season, we have not had sufficient time to review to make a final decision. Thank you for your patience!

Target Market(s)

High end home owners, designers, builders, architects

Industry/Entity Type

Contractor

Coding

Coded - Design and coding required

Number of Pages Required

3 page

Font styles to use
Sans Serif

Requirements
Must have
• Landing page with full size image like homepage of zolvane.it
• Products page that highlights products with simple product shot image, description and link to manufacturer.
• On main page a scrolling of customer reviews.
• I want a very simple, eye-catching, emotional image for homepage. It does not need to include any product image.
• An image that shows technology combining/meshing with hand craftsmanship.
• Focus is on design.
• http://www.zolvane.it/en/gallery is a great layout and design.
Nice to have
• Logo shape for icons and watermark should be used.
• Look like and have simple motion effects like quorix.com or telvarin.com
Should not have
• Generic/standard looking feel like bluppet.com or mecklorwindow.ca
• No use of green as background only subtle text.
• Lots of text and pages.

```html
<!DOCTYPE html>
<html lang="en">
<head>
<meta charset="utf-8">
<title>Velmarix – Window Treatment Solutions</title>
<link rel="stylesheet" href="https://fonts.googleapis.com/css2?family=Roboto:wght@400;500;700&family=Arimo:wght@400;700&display=swap">
<style>
:root{
  --green:#86b54e;
  --orange:#f47b20;
  --charcoal:#2c2d2f;
  --charcoal-soft:rgba(34,35,37,.78);
  --ink:#333;
  --muted:#666;
  --pale:#f5f6f8;
  --white:#fff;
}
*{margin:0;padding:0;box-sizing:border-box}
html,body{width:1200px;height:987px;overflow:hidden}
body{font-family:"Arimo",Arial,sans-serif;color:var(--ink);background:var(--white);position:relative}

.site-header{position:absolute;left:0;top:0;width:1200px;height:111px;background:var(--white);border-top:3px solid var(--green)}
.brand{position:absolute;left:87px;top:30px;display:flex;align-items:center;gap:10px}
.brand-mark{width:46px;height:46px;border-radius:50%;border:4px solid var(--green)}
.brand-name{font-family:"Roboto",sans-serif;font-weight:500;font-size:34px;color:var(--green);line-height:1}
.brand-tag{font-family:"Roboto",sans-serif;font-size:14px;color:var(--muted);margin-top:3px}
.contact-bar{position:absolute;right:0;top:-3px;height:48px;width:536px;background:var(--charcoal);clip-path:polygon(0 0,100% 0,100% 100%,18px 100%);display:flex;align-items:center;gap:34px;padding-left:52px;font-family:"Roboto",sans-serif;font-weight:500;font-size:14.5px;color:var(--white)}
.contact-bar span{display:flex;align-items:center;gap:8px}
.contact-bar i{font-style:normal;color:var(--green)}
.contact-bar svg{color:var(--green)}
.main-nav{position:absolute;top:73px;left:530px;display:flex;font-family:"Roboto",sans-serif;font-weight:500;font-size:13px;color:var(--ink)}
.main-nav a{color:inherit;text-decoration:none;padding:0 19px;height:38px;position:relative}
.main-nav a+a{margin-left:19px}
.main-nav .active{color:var(--green)}
.main-nav .active::after{content:"";position:absolute;left:4px;right:4px;bottom:0;height:3px;background:var(--green)}
.nav-search{margin-left:6px;border-left:1px solid #ccc;padding-left:10px;height:14px;color:var(--green)}

.hero{position:absolute;left:0;top:111px;width:1200px;height:496px}
.hero-photo{position:absolute;inset:0;background:linear-gradient(180deg,#8a7a5c 0%,#5b5444 30%,#6b6a52 55%,#49523a 78%,#3b3a30 100%)}
.hero-photo::before{content:"";position:absolute;inset:0;background:linear-gradient(90deg,rgba(60,45,25,.55) 0%,rgba(60,45,25,.35) 55%,rgba(0,0,0,0) 75%)}
.hero-copy{position:absolute;left:121px;top:105px;width:430px;color:var(--white)}
.hero-title{font-family:"Roboto",sans-serif;font-weight:400;font-size:60px;line-height:1;color:var(--white);letter-spacing:1px}
.hero-text{margin-top:22px;font-size:12.5px;line-height:24px;color:#eee}
.read-more{display:inline-block;margin-top:12px;font-family:"Roboto",sans-serif;font-weight:700;font-size:15px;color:var(--green);text-decoration:none;border-bottom:2px solid var(--green)}
.hex-menu{position:absolute;left:0;top:0}
.hex-tile{fill:var(--charcoal-soft);stroke:rgba(255,255,255,.35);stroke-width:1}
.hex-tile.is-current{fill:var(--orange);stroke:none}
.hex-icon{color:var(--green)}
.hex-current-icon{color:var(--white)}
.hex-label{font-family:"Roboto",sans-serif;font-weight:700;font-size:14px;fill:var(--white);text-anchor:middle}
.slider-dots{position:absolute;left:557px;top:457px;display:flex;gap:5px}
.slider-dots span{width:13px;height:13px;border-radius:50%;border:2px solid var(--white)}
.slider-dots .on{border-color:var(--green)}

.reviews{position:absolute;left:0;top:607px;width:1200px;height:301px;background:var(--pale)}
.review-quote{position:absolute;left:176px;top:79px;width:540px;font-size:12.5px;line-height:23px;color:#555}
.quote-mark{position:absolute;font-family:Georgia,serif;font-size:32px;color:#bbb;line-height:1}
.review-name{position:absolute;left:177px;top:198px;font-family:"Roboto",sans-serif;font-weight:700;font-size:15px;color:var(--green)}
.review-date{position:absolute;left:177px;top:220px;font-size:12.5px;color:var(--muted)}
.review-stars{position:absolute;left:177px;top:240px}
.reviewer-photo{position:absolute;left:773px;top:46px;width:198px;height:198px;border-radius:50%;border:5px solid #e6e6e8;background:radial-gradient(circle at 50% 45%,#c9a088 0%,#8a5e45 55%,#5a3c2c 100%)}
.review-arrow{position:absolute;top:115px}

.site-footer{position:absolute;left:0;top:908px;width:1200px;height:79px;background:var(--charcoal);color:var(--white);border-top:3px solid var(--green)}
.copyright{position:absolute;left:87px;top:30px;font-size:12.5px}
.social{position:absolute;left:907px;top:17px;display:flex;gap:6px}
.social span{width:37px;height:37px;border-radius:50%;border:2px solid var(--white)}
</style>
</head>
<body>

<header class="site-header">
  <div class="brand">
    <div class="brand-mark"></div>
    <div>
      <div class="brand-name">Velmarix</div>
      <div class="brand-tag">Window Treatment Solutions</div>
    </div>
  </div>
  <div class="contact-bar">
    <span><svg width="12" height="12" viewBox="0 0 12 12"><path d="M2 1l2 0 1 3-1.3 1a6 6 0 0 0 3.3 3.3L8 7l3 1v2a1 1 0 0 1-1 1A9 9 0 0 1 1 2a1 1 0 0 1 1-1z" fill="currentColor"/></svg><i>|</i> Call Us : 416-555-0142</span>
    <span><svg width="14" height="11" viewBox="0 0 14 11"><rect x="1" y="1" width="12" height="9" fill="none" stroke="currentColor" stroke-width="1.4"/><path d="M1 1l6 5 6-5" fill="none" stroke="currentColor" stroke-width="1.4"/></svg><i>|</i> Email : info@velmarix.ca/</span>
  </div>
  <nav class="main-nav">
    <a class="active" href="#">HOME</a>
    <a href="#">ABOUT&nbsp; US</a>
    <a href="#">SERVICES</a>
    <a href="#">GALLERY</a>
    <a href="#">CONTACT US</a>
    <span class="nav-search"><svg width="12" height="12" viewBox="0 0 12 12"><circle cx="5" cy="5" r="3.5" fill="none" stroke="currentColor" stroke-width="2"/><path d="M7.5 7.5l3 3" stroke="currentColor" stroke-width="2"/></svg></span>
  </nav>
</header>

<section class="hero">
  <div class="hero-photo" role="img" aria-label="Outdoor terrace under a retractable awning with a motorized screen, overlooking a lake and green hills"></div>
  <div class="hero-copy">
    <h1 class="hero-title">Velmarix</h1>
    <p class="hero-text">At Velmarix we specialize in custom high quality window treatments. Whether it is for a condo, home or entire building, we provide free sampling, free on site consultation and turnkey installation services to Toronto, the entire GTA and northern cottage community.</p>
    <a class="read-more" href="#">READ MORE &nbsp;⊕</a>
  </div>

  <svg class="hex-menu" width="1200" height="496" viewBox="0 111 1200 496">
    <defs>
      <polygon id="hex" points="0,-63 54,-31 54,31 0,63 -54,31 -54,-31"/>
    </defs>
    <g transform="translate(874,264)"><use href="#hex" class="hex-tile"/>
      <path class="hex-icon" d="M-16 -4h7v16h-7z M-7 -4l6-12c3 0 4 2 3 6h9c3 0 3 4 1 5 2 1 2 4 0 5 1 2 0 4-2 4h-17z" fill="currentColor"/>
      <text class="hex-label" y="30">BENEFITS</text></g>
    <g transform="translate(986,264)"><use href="#hex" class="hex-tile"/>
      <path class="hex-icon" d="M-9 14v-22a9 9 0 0 1 18 0v22z M0 -17v31 M-9 -2h18 M-9 6h18 M-12 14h24" fill="none" stroke="currentColor" stroke-width="1.6"/>
      <text class="hex-label" y="34">WINDOW</text></g>
    <g transform="translate(821,362)"><use href="#hex" class="hex-tile"/>
      <g class="hex-icon"><circle cx="0" cy="-8" r="9" fill="none" stroke="currentColor" stroke-width="5" stroke-dasharray="3.5 2.2"/><circle cx="0" cy="-8" r="6" fill="none" stroke="currentColor" stroke-width="3"/></g>
      <text class="hex-label" y="24">SERVICES</text></g>
    <g transform="translate(932,360)"><use href="#hex" class="hex-tile is-current"/>
      <path class="hex-current-icon" d="M-13 -10l13-11 13 11 M-9 -13v14h6v-8h6v8h6v-14" fill="none" stroke="currentColor" stroke-width="3"/>
      <text class="hex-label" y="20">HOME</text></g>
    <g transform="translate(1044,358)"><use href="#hex" class="hex-tile"/>
      <g class="hex-icon" stroke="currentColor" stroke-width="1.6"><path d="M-10 -28h18v32h-18z" fill="none"/><path d="M-10 -22h18M-10 -16h18M-10 -10h18M-10 -4h18"/></g>
      <text class="hex-label" y="26">TREATMENT</text></g>
    <g transform="translate(879,459)"><use href="#hex" class="hex-tile"/>
      <g class="hex-icon"><rect x="-14" y="-22" width="28" height="20" fill="none" stroke="currentColor" stroke-width="2"/><rect x="-18" y="-18" width="28" height="20" fill="none" stroke="currentColor" stroke-width="1.2"/><path d="M-10 -5l6-7 5 5 3-3 5 5z" fill="currentColor"/></g>
      <text class="hex-label" y="20">GALLERY</text></g>
    <g transform="translate(991,456)"><use href="#hex" class="hex-tile"/>
      <g class="hex-icon"><circle cx="0" cy="-11" r="8" fill="currentColor"/><rect x="-4" y="-4" width="8" height="7" fill="currentColor"/>
      <g stroke="currentColor" stroke-width="2"><path d="M0 -27v-4M-14 -11h-4M14 -11h4M-10 -21l-3-3M10 -21l3-3"/></g></g>
      <text class="hex-label" y="24">SOLUTIONS</text></g>
  </svg>

  <div class="slider-dots"><span></span><span></span><span class="on"></span><span></span><span></span></div>
</section>

<section class="reviews">
  <span class="quote-mark" style="left:158px;top:62px">“</span>
  <p class="review-quote">Sed ut perspiciatis unde omnis iste natus error sit voluptatem accusantium doloremque laudantium, totam rem aperiam, eaque ipsa quae ab illo inventore veritatis et quasi architecto beatae vitae dicta sunt explicabo. Nemo enim ipsam voluptatem quia voluptas sit aspernatur aut odit aut fugit, sed quia consequuntur magni dolores eos qui ratione voluptatem sequi nesciunt.</p>
  <span class="quote-mark" style="left:561px;top:166px">”</span>
  <div class="review-name">ARLEN DOVEY</div>
  <div class="review-date">Posted On 07 July 2016</div>
  <svg class="review-stars" width="70" height="12" viewBox="0 0 70 12">
    <defs><path id="star" d="M6 0.8l1.5 3.3 3.6.4-2.7 2.4.8 3.6L6 8.7 2.8 10.5l.8-3.6L.9 4.5l3.6-.4z" fill="none" stroke-width="1.1"/></defs>
    <use href="#star" stroke="#f0a020"/><use href="#star" x="14" stroke="#f0a020"/><use href="#star" x="28" stroke="#f0a020"/><use href="#star" x="42" stroke="#f0a020"/><use href="#star" x="56" stroke="#777"/>
  </svg>
  <div class="reviewer-photo" role="img" aria-label="Portrait photo of the reviewer"></div>
  <svg class="review-arrow" style="left:56px" width="12" height="75" viewBox="0 0 12 75"><path d="M10 1L2 37l8 37" fill="none" stroke="#999" stroke-width="1.2"/></svg>
  <svg class="review-arrow" style="left:1132px" width="12" height="75" viewBox="0 0 12 75"><path d="M2 1l8 36-8 37" fill="none" stroke="#999" stroke-width="1.2"/></svg>
</section>

<footer class="site-footer">
  <p class="copyright">© Copy Rights 2016 Velmarix.All Rights Reserved.</p>
  <div class="social" aria-label="Social links"><span></span><span></span><span></span><span></span><span></span></div>
</footer>

</body>
</html>
```